Book cover for book about Climate Change

Looking for a clean, bold, and attractive cover for a mass-market paperback (5.5"x 8.5") about solving the climate change problem. Title is either "Where the Rivers Meet” or A Harbor Made of Glass” (your choice), subtitle is "A practical field guide to mending the weather — so that the young ones after us inherit steady seasons and open skies," author is Lorne Whitcombe. Thinking that it *might* feature an image of Earth (or a portion thereof) and its very thin layer of atmosphere -- but STRONGLY encourage other ideas too!

Requirements
Nice to have
• Keep it positive — NOT scary doom-and-gloom

```html
<!DOCTYPE html>
<html lang="en">
<head>
<meta charset="utf-8">
<title>Where the Rivers Meet — Lorne Whitcombe</title>
<link rel="stylesheet" href="https://fonts.googleapis.com/css2?family=Poppins:wght@400;500;600;700;800&display=swap">
<style>
  :root {
    --backdrop: #c6c6c6;
    --paper: #ffffff;
    --leaf: #3aa047;
    --leaf-bright: #4cc765;
    --lagoon: #20968a;
    --lagoon-mid: #3dbaac;
    --lagoon-soft: #8ad7cd;
    --sun: #fcc419;
    --poppy: #e23b2a;
    --ink: #222222;
  }
  * { margin: 0; padding: 0; box-sizing: border-box; }
  html, body {
    width: 1200px; height: 1200px; overflow: hidden;
    background: var(--backdrop);
  }
  .book-cover {
    position: absolute; left: 247px; top: 51px;
    width: 706px; height: 1092px;
    background: var(--paper);
    overflow: hidden;
  }
  .title-block {
    position: absolute; left: 0; top: 0;
    width: 706px; height: 450px;
  }
  .title-small {
    font-family: "Poppins", sans-serif; font-weight: 700;
    fill: var(--lagoon);
  }
  .title-large {
    font-family: "Poppins", sans-serif; font-weight: 800;
    fill: var(--leaf);
  }
  .title-rule { stroke: var(--lagoon); stroke-width: 2.5; }
  .subtitle {
    position: absolute; left: 80px; top: 446px; width: 546px;
    font-family: "Poppins", sans-serif; font-weight: 500;
    font-size: 21.5px; line-height: 31.5px;
    color: var(--ink); text-align: center;
  }
  .subtitle-lead { color: var(--leaf); font-weight: 600; }
  .ground {
    position: absolute; left: 0; top: 780px;
    width: 706px; height: 235px;
  }
  .ground-fill { fill: var(--lagoon-soft); }
  .cover-artwork {
    position: absolute; left: 10px; top: 560px;
    width: 686px; height: 300px;
    background: linear-gradient(90deg,
      #9fdcd3 0%, var(--sun) 24%, #ffe9a6 36%,
      var(--lagoon-mid) 52%, #bfe9e2 64%,
      #f39a8c 78%, var(--lagoon-mid) 100%);
    -webkit-mask-image: radial-gradient(ellipse 52% 50% at 50% 52%, #000 55%, transparent 100%);
            mask-image: radial-gradient(ellipse 52% 50% at 50% 52%, #000 55%, transparent 100%);
    opacity: 0.85;
  }
  .author-band {
    position: absolute; left: 0; top: 1015px;
    width: 706px; height: 77px;
    background: linear-gradient(90deg, var(--leaf) 0%, var(--leaf-bright) 50%, var(--leaf) 100%);
    display: flex; align-items: center; justify-content: center;
  }
  .author-name {
    font-family: "Poppins", sans-serif; font-weight: 700;
    font-size: 38px; letter-spacing: 0.3em;
    color: #ffffff; text-transform: uppercase;
    margin-right: -0.3em;
  }
</style>
</head>
<body>
  <main class="book-cover">
    <svg class="title-block" viewBox="0 0 706 450" aria-labelledby="book-title">
      <title id="book-title">Where the Rivers Meet</title>
      <line class="title-rule" x1="88" y1="65" x2="176" y2="65"/>
      <line class="title-rule" x1="530" y1="65" x2="617" y2="65"/>
      <text class="title-small" x="188" y="87" font-size="62" textLength="330" lengthAdjust="spacingAndGlyphs">WHERE THE</text>
      <text class="title-large" x="86" y="226" font-size="162" textLength="532" lengthAdjust="spacingAndGlyphs">RIVERS</text>
      <line class="title-rule" x1="88" y1="262" x2="617" y2="262"/>
      <text class="title-large" x="86" y="435" font-size="200" textLength="532" lengthAdjust="spacingAndGlyphs">MEET</text>
    </svg>

    <p class="subtitle">
      <span class="subtitle-lead">A PRACTICAL FIELD GUIDE</span> to mending the weather — so that the young ones after us inherit steady seasons and open skies
    </p>

    <div class="cover-artwork" role="img" aria-label="Cheerful illustration of children holding a sun, a water drop, a wind turbine and the Earth around a recycling symbol"></div>

    <svg class="ground" viewBox="0 0 706 235" preserveAspectRatio="none" aria-hidden="true">
      <path class="ground-fill" d="M0 97 Q330 20 706 76 L706 235 L0 235 Z"/>
    </svg>

    <footer class="author-band">
      <span class="author-name">Lorne Whitcombe</span>
    </footer>
  </main>
</body>
</html>
```